TalkHarbor - Language Coaching Services

Sleek, innovative, trendy design for Language Coaching business.

TalkHarbor is a new UK based company that provides Language Coaching services. We offer highly personalized on-line and face to face language courses. We also impart learning techniques workshops based on the latest neuroscience research for second-language acquisition.

Target Market(s)

See attached info

Industry/Entity Type

Consulting

Contact Information for Business Card

TalkHarbor
DaniaKV@talkharbor.co.uk
TalkHarbor.co.uk
London, UK

Font styles to use
Sans Serif

```html
<!DOCTYPE html>
<html lang="en">
<head>
<meta charset="utf-8">
<title>TalkHarbor – Business Card</title>
<link rel="stylesheet" href="https://fonts.googleapis.com/css2?family=Work+Sans:wght@400;500;600&display=swap">
<style>
  :root {
    --page: #1c1c1e;
    --card: #232325;
    --card-edge: #2c2c2f;
    --blue: #1a9ad6;
    --blue-bright: #1fb0ea;
    --white: #f2f2f2;
  }
  * { margin: 0; padding: 0; box-sizing: border-box; }
  html, body { width: 1200px; height: 900px; overflow: hidden; }
  body {
    background: var(--page);
    font-family: "Work Sans", Arial, sans-serif;
    color: var(--white);
    position: relative;
  }
  .card {
    position: absolute;
    left: 250px;
    width: 700px;
    height: 400px;
    background: linear-gradient(135deg, var(--card) 0%, var(--card-edge) 70%, var(--card) 100%);
  }
  .card--front { top: 35px; }
  .card--back { top: 465px; }

  /* front */
  .front-brand {
    position: absolute;
    left: 0; right: 0; top: 95px;
    display: flex; flex-direction: column; align-items: center;
  }
  .brand-ring {
    width: 110px; height: 110px;
    border: 9px solid var(--blue);
    border-radius: 50%;
  }
  .brand-name {
    font-weight: 500;
    color: var(--blue);
    letter-spacing: 2px;
    text-transform: uppercase;
  }
  .front-brand .brand-name { font-size: 44px; margin-top: 14px; }
  .front-web {
    position: absolute;
    left: 0; right: 0; bottom: 62px;
    text-align: center;
    font-size: 15px;
    letter-spacing: 1.5px;
  }
  .accent { color: var(--blue-bright); }

  /* back */
  .back-brand {
    position: absolute;
    left: 30px; top: 105px; width: 300px;
    display: flex; flex-direction: column; align-items: center;
  }
  .back-brand .brand-ring { width: 120px; height: 120px; border-width: 10px; }
  .back-brand .brand-name { font-size: 40px; margin-top: 14px; }
  .divider {
    position: absolute;
    left: 370px; top: 80px;
    width: 2px; height: 240px;
    background: var(--white);
  }
  .contact {
    position: absolute;
    left: 405px; top: 82px;
  }
  .contact-name {
    font-size: 27px; font-weight: 500;
    color: var(--blue-bright);
    letter-spacing: 2px;
    text-transform: uppercase;
  }
  .contact-role { font-size: 17px; letter-spacing: 1px; margin-top: 2px; }
  .contact-address {
    font-size: 17px; line-height: 25px; letter-spacing: 1.5px;
    margin-top: 18px;
    font-style: normal;
  }
  .contact-list { list-style: none; margin-top: 12px; }
  .contact-list li {
    display: flex; align-items: center; gap: 10px;
    font-size: 17px; line-height: 27px; letter-spacing: 1.3px;
  }
  .contact-list svg { width: 13px; height: 13px; flex: none; }
</style>
</head>
<body>

<section class="card card--front">
  <div class="front-brand">
    <div class="brand-ring"></div>
    <div class="brand-name">TalkHarbor</div>
  </div>
  <div class="front-web">www.<span class="accent">talkharbor</span>.co.uk</div>
</section>

<section class="card card--back">
  <div class="back-brand">
    <div class="brand-ring"></div>
    <div class="brand-name">TalkHarbor</div>
  </div>
  <div class="divider"></div>
  <div class="contact">
    <div class="contact-name">Elena Ward</div>
    <div class="contact-role">Director</div>
    <address class="contact-address">42 Harbour Lane,<br>London, UK, E14 5AB</address>
    <ul class="contact-list">
      <li>
        <svg viewBox="0 0 16 16" aria-hidden="true"><path d="M4 1.5 6.5 4 5 6c.8 1.8 2.2 3.2 4 4l2-1.5 2.5 2.5-1.8 2C7 12.5 3.5 9 2 3.3z" fill="none" stroke="#1fb0ea" stroke-width="1.4"/></svg>
        (020) 555-0147
      </li>
      <li>
        <svg viewBox="0 0 16 16" aria-hidden="true"><rect x="1.5" y="3.5" width="13" height="9" fill="none" stroke="#1fb0ea" stroke-width="1.4"/><path d="M1.5 3.5 8 9l6.5-5.5" fill="none" stroke="#1fb0ea" stroke-width="1.4"/></svg>
        info@talkharbor.co.uk
      </li>
      <li>
        <svg viewBox="0 0 16 16" aria-hidden="true"><circle cx="8" cy="8" r="6.5" fill="none" stroke="#1fb0ea" stroke-width="1.3"/><ellipse cx="8" cy="8" rx="3" ry="6.5" fill="none" stroke="#1fb0ea" stroke-width="1.1"/><path d="M1.5 8h13" stroke="#1fb0ea" stroke-width="1.1"/></svg>
        <span>www.<span class="accent">talkharbor</span>.co.uk</span>
      </li>
    </ul>
  </div>
</section>

</body>
</html>
```